Cozy Cradle Loops Needs a Beautiful Website

I need a new website for this new E-commerce. I sell handmade baby crochets, e.g. booties, headbands, hats, etc. I need a feminine and soft design to make the moms-to-be say 'oohh ahh'. I'd like pink, blue and gray. I'd like an inviting homepage, and nice regular pages where people can see and order the products.

Industry/Entity Type

Baby

Requirements
Must have
• beautiful, soft, feminine design. Please use pictures of the colors I'd like: brown, yellow, pink and blue. Any combination, but definitely include brown.

```html
<!DOCTYPE html>
<html lang="en">
<head>
<meta charset="utf-8">
<title>Cozy Cradle Loops</title>
<link href="https://fonts.googleapis.com/css2?family=Mulish:wght@400;600&family=Varela+Round&display=swap" rel="stylesheet">
<style>
:root{
  --pink:#e8348c;
  --pink-text:#e4157f;
  --blue:#3ec1e2;
  --blue-dark:#32afd0;
  --gray-bar:#f1f1f1;
  --panel:#f7f7f7;
  --text:#555;
  --tan:#d6c7b4;
  --white:#fff;
}
*{box-sizing:border-box;margin:0;padding:0}
html,body{width:975px;height:1200px;overflow:hidden}
body{position:relative;font-family:"Mulish",sans-serif;color:var(--text);background:var(--white)}
.backdrop-top{position:absolute;left:0;top:0;width:975px;height:396px;background:linear-gradient(#f1f3f0,#fafafa)}
.backdrop-band{position:absolute;left:0;top:396px;width:975px;height:220px;background:var(--blue)}
.page{position:absolute;left:60px;top:0;width:855px}
.top-bar{height:28px;background:var(--gray-bar);display:flex;justify-content:flex-end;align-items:center;font-size:10px;color:#666;padding-right:15px}
.top-bar span.sep{margin:0 16px}
.header{height:80px;background:var(--white);position:relative}
.brand{position:absolute;left:16px;top:26px;font-family:"Varela Round",sans-serif;font-size:22px;color:var(--pink);display:flex;align-items:center;gap:8px}
.brand .dot{width:14px;height:14px;border-radius:50%;background:var(--blue)}
.search{position:absolute;left:424px;top:28px;width:270px;height:28px;display:flex}
.search-field{flex:1;border:1px solid #ccc;font-size:10px;color:#888;padding:8px 11px}
.search-btn{width:31px;background:var(--blue);display:flex;align-items:center;justify-content:center}
.cart{position:absolute;left:702px;top:28px;width:139px;height:28px;background:var(--pink);color:#fff;font-size:10px;display:flex;align-items:center;justify-content:center}
.nav{height:32px;background:var(--blue);display:flex;align-items:center;font-size:10px;color:#fff;padding-left:17px}
.nav a{margin-right:56px}
.hero{position:absolute;top:151px;left:0;width:855px;height:320px;background:linear-gradient(90deg,#f4f4f4,#e9ebec 60%,#e4e4e2);overflow:hidden}
.hero-photo{position:absolute;left:420px;top:0;width:435px;height:320px;background:radial-gradient(circle at 70% 45%,#f3c21d 0,#f0b81c 22%,transparent 40%),radial-gradient(circle at 22% 50%,#e8542a 0,#e36a35 18%,transparent 32%),linear-gradient(90deg,rgba(233,235,236,0),#e0e2e0)}
.hero h1{position:absolute;left:34px;top:88px;width:420px;font-family:"Varela Round",sans-serif;font-weight:400;font-size:32px;line-height:35px;color:var(--pink-text)}
.hero p{position:absolute;left:34px;top:164px;font-family:"Varela Round",sans-serif;font-size:22px;color:#333}
.hero .btn{position:absolute;left:34px;top:215px;width:138px;height:33px;background:var(--blue);color:#fff;font-family:"Varela Round",sans-serif;font-size:16px;display:flex;align-items:center;justify-content:center}
.dots{position:absolute;left:34px;top:291px;display:flex;gap:5px}
.dots i{width:7px;height:7px;border-radius:2px;background:#555}
.dots i.on{background:var(--pink)}
.featured{position:absolute;top:490px;left:0;width:855px;height:324px;background:var(--panel)}
.featured h2{position:absolute;left:20px;top:22px;font-family:"Varela Round",sans-serif;font-weight:400;font-size:18px;color:var(--pink)}
.swatches{position:absolute;left:586px;top:26px;display:flex;align-items:center;gap:4px;font-size:9px;color:#444}
.swatches .lbl{margin-right:3px}
.swatches i{width:13px;height:13px}
.card{position:absolute;top:57px;width:176px;height:246px;background:#fff;border:1px solid #e3e3e3}
.card .photo{position:absolute;left:12px;top:12px;width:152px;height:136px}
.card h3{position:absolute;left:12px;top:156px;font-family:"Varela Round",sans-serif;font-weight:400;font-size:14px;color:var(--blue)}
.card p{position:absolute;left:12px;top:176px;width:150px;font-size:10px;line-height:15px;color:#555}
.card .price{position:absolute;left:12px;top:215px;font-size:14px;color:var(--pink)}
.card .basket{position:absolute;left:64px;top:210px;width:28px;height:26px;background:var(--pink);display:flex;align-items:center;justify-content:center}
.card .details{position:absolute;left:92px;top:210px;width:70px;height:26px;background:#e6e6e6;font-size:11px;color:#333;display:flex;align-items:center;justify-content:center}
.category{position:absolute;top:814px;width:282px;height:142px;background:var(--tan);overflow:hidden}
.category .photo{position:absolute;left:0;top:0;width:140px;height:142px}
.category h3{position:absolute;top:22px;font-family:"Varela Round",sans-serif;font-weight:400;font-size:22px;color:#222}
.category p{position:absolute;top:48px;width:130px;font-size:10px;line-height:15px;color:#fff}
.category .btn{position:absolute;top:108px;width:74px;height:22px;background:var(--pink);color:#fff;font-size:11px;display:flex;align-items:center;justify-content:center}
.footer{position:absolute;left:0;top:958px;width:975px;height:202px;background:var(--blue);color:#fff}
.footer .col{position:absolute;top:22px}
.footer h4{font-family:"Varela Round",sans-serif;font-weight:400;font-size:14px;margin-bottom:6px}
.footer li{list-style:none;font-size:9px;line-height:18.8px}
.news-input{position:absolute;left:544px;top:54px;width:225px;height:29px;background:#fff;color:#555;font-size:9px;font-style:italic;padding:9px 13px}
.news-btn{position:absolute;left:780px;top:54px;width:80px;height:29px;background:var(--pink)}
.connect{position:absolute;left:544px;top:100px}
.social{position:absolute;left:544px;top:128px;display:flex;gap:6px}
.social i{width:24px;height:24px;border-radius:50%}
.bottom-bar{position:absolute;left:0;top:1160px;width:975px;height:40px;background:var(--blue-dark);color:#fff;font-size:9px}
.bottom-bar .copy{position:absolute;left:60px;top:15px}
.pay{position:absolute;left:708px;top:8px;display:flex;gap:5px}
.pay i{width:38px;height:22px;background:#fff;border-radius:2px}
</style>
</head>
<body>
<div class="backdrop-top" role="img" aria-label="Soft festive backdrop with snowflakes and stars"></div>
<div class="backdrop-band"></div>

<div class="page">
  <div class="top-bar">
    <span>My Account</span><span class="sep">|</span><span>My Wishlist</span><span class="sep">|</span><span>Checkout</span><span class="sep">|</span><span>Log In</span>
  </div>
  <div class="header">
    <div class="brand"><span class="dot"></span>Cozy Cradle Loops</div>
    <div class="search">
      <div class="search-field">Search..keyword..</div>
      <div class="search-btn"><svg width="14" height="14" viewBox="0 0 14 14"><circle cx="5.5" cy="5.5" r="4" fill="none" stroke="#fff" stroke-width="2"/><line x1="8.5" y1="8.5" x2="13" y2="13" stroke="#fff" stroke-width="2.4"/></svg></div>
    </div>
    <div class="cart">My Cart:&nbsp; 0 item(s) - $0.00</div>
  </div>
  <div class="nav"><a>HOME</a><a>ABOUT US</a><a>PRODUCTS</a><a>ACCESSORIES</a><a>SPECIALS</a><a>CONTACT US</a></div>

  <section class="hero">
    <div class="hero-photo" role="img" aria-label="Orange crochet baby booties beside a yellow yarn ball with a crochet hook"></div>
    <h1>We Sell Handmade Baby Crochets</h1>
    <p>e.g. Booties, Headbands, Hats, etc.</p>
    <div class="btn">Shop Now ››</div>
    <div class="dots"><i class="on"></i><i></i><i></i><i></i></div>
  </section>

  <section class="featured">
    <h2>FEATURED PRODUCTS</h2>
    <div class="swatches"><span class="lbl">SHOP BY COLORS:</span>
      <i style="background:#f6993c"></i><i style="background:#ef6fc8"></i><i style="background:#56c05a"></i><i style="background:#f03878"></i><i style="background:#5cc4d8"></i><i style="background:#f47f96"></i><i style="background:#ef2f3c"></i><i style="background:#b9d35a"></i><i style="background:#dd1530"></i><i style="background:#fbdbe2"></i>
    </div>

    <div class="card" style="left:21px">
      <div class="photo" role="img" aria-label="Black and white crochet sneaker booties" style="background:linear-gradient(135deg,#8a8a8a,#2a2a2a 60%,#6a6a6a)"></div>
      <h3>Product Name</h3><p>Sed ut perspiciatis unde omnis iste natus...</p>
      <span class="price">$12.00</span>
      <div class="basket"><svg width="14" height="12" viewBox="0 0 14 12"><path d="M1 4h12l-2 7H3z M4 4l3-3 3 3" fill="#fff" stroke="#fff" stroke-width="1"/></svg></div>
      <div class="details">Details</div>
    </div>
    <div class="card" style="left:235px">
      <div class="photo" role="img" aria-label="Pink crochet crown headband" style="background:radial-gradient(circle at 50% 50%,#f07ad0,#f1eaf0 65%)"></div>
      <h3>Product Name</h3><p>Sed ut perspiciatis unde omnis iste natus...</p>
      <span class="price">$12.00</span>
      <div class="basket"><svg width="14" height="12" viewBox="0 0 14 12"><path d="M1 4h12l-2 7H3z M4 4l3-3 3 3" fill="#fff" stroke="#fff" stroke-width="1"/></svg></div>
      <div class="details">Details</div>
    </div>
    <div class="card" style="left:449px">
      <div class="photo" role="img" aria-label="Pink crochet ballet slippers with roses" style="background:linear-gradient(160deg,#e8dcd8,#f0b8c8 55%,#ddd)"></div>
      <h3>Product Name</h3><p>Sed ut perspiciatis unde omnis iste natus...</p>
      <span class="price">$12.00</span>
      <div class="basket"><svg width="14" height="12" viewBox="0 0 14 12"><path d="M1 4h12l-2 7H3z M4 4l3-3 3 3" fill="#fff" stroke="#fff" stroke-width="1"/></svg></div>
      <div class="details">Details</div>
    </div>
    <div class="card" style="left:663px">
      <div class="photo" role="img" aria-label="Gray crochet shoes with red roses" style="background:linear-gradient(160deg,#d9d9d9,#6d6a66 55%,#a09a95)"></div>
      <h3>Product Name</h3><p>Sed ut perspiciatis unde omnis iste natus...</p>
      <span class="price">$12.00</span>
      <div class="basket"><svg width="14" height="12" viewBox="0 0 14 12"><path d="M1 4h12l-2 7H3z M4 4l3-3 3 3" fill="#fff" stroke="#fff" stroke-width="1"/></svg></div>
      <div class="details">Details</div>
    </div>
  </section>

  <div class="category" style="left:0">
    <div class="photo" role="img" aria-label="Sleeping baby wearing a blue crochet crown" style="background:linear-gradient(90deg,#c9c0b5,#e2d2c2 70%,var(--tan))"></div>
    <h3 style="left:140px">HeadBands</h3>
    <p style="left:141px">Sed ut perspiciatis unde omnis iste natus error sit voluptatem..</p>
    <div class="btn" style="left:142px">Shop Now</div>
  </div>
  <div class="category" style="left:287px">
    <div class="photo" role="img" aria-label="Navy crochet sneaker booties with red stars" style="background:linear-gradient(90deg,#6b6f78,#4a5060 60%,var(--tan))"></div>
    <h3 style="left:143px">Booties</h3>
    <p style="left:144px">Sed ut perspiciatis unde omnis iste natus error sit voluptatem..</p>
    <div class="btn" style="left:145px">Shop Now</div>
  </div>
  <div class="category" style="left:574px">
    <div class="photo" style="width:150px;background:linear-gradient(120deg,#6a5a52,#d8b0c8 50%,#f0b070 80%,var(--tan))" role="img" aria-label="Assorted crochet booties and colorful crown headbands"></div>
    <h3 style="left:146px">Collections</h3>
    <p style="left:147px">Sed ut perspiciatis unde omnis iste natus error sit voluptatem..</p>
    <div class="btn" style="left:149px">Shop Now</div>
  </div>
</div>

<footer class="footer">
  <div class="col" style="left:60px"><h4>Information</h4><ul><li>About Us</li><li>Customer Service</li><li>Privacy Policy</li><li>Site Map</li><li>Search Terms</li><li>Advanced Search</li><li>Orders and Returns</li><li>Contact Us</li></ul></div>
  <div class="col" style="left:209px"><h4>Why Buy from Us</h4><ul><li>Shipping &amp; Returns</li><li>Secure Shopping</li><li>International Shipping</li><li>Affiliates</li><li>Group Sales</li></ul></div>
  <div class="col" style="left:382px"><h4>My Account</h4><ul><li>Sign In</li><li>View Cart</li><li>My Wishlist</li><li>Track My Order</li><li>Help</li></ul></div>
  <div class="col" style="left:544px"><h4>Newsletter Signup</h4></div>
  <div class="news-input">Enter Email Address</div>
  <div class="news-btn"></div>
  <div class="connect"><h4>Connect Us</h4></div>
  <div class="social"><i style="background:#3b5998"></i><i style="background:#1da1f2"></i><i style="background:#d62020"></i></div>
</footer>

<div class="bottom-bar">
  <span class="copy">Copyright ©. Company Name. All Right Reserved</span>
  <div class="pay"><i></i><i></i><i></i><i></i><i></i></div>
</div>
</body>
</html>
```